Looking for a cool & simple business-card-design for digital agency

Hi!

We are a web agency that offers Reputation Management, Vextor & Seo Services and software development. We like cool things, we like innovative styles.

We have uploaded our logo.

Project Deadline Extended Reason: Client does not want any designs with the colorful logo. Please send us submissions ONLY with the blac and white logo. What the client would like to see:1) Back of the card: is a silver logo on a black background2) front of the card with all the data, please use white background and black logo thank you Added Friday, May 8, 2015

Industry/Entity Type

Software

```html
<!DOCTYPE html>
<html lang="en">
<head>
<meta charset="utf-8">
<title>Nordlink Stationery</title>
<link rel="stylesheet" href="https://fonts.googleapis.com/css2?family=Open+Sans:wght@400;600;700&display=swap">
<style>
  :root{
    --bg:#e6e6e6;
    --paper:#ffffff;
    --ink:#111111;
    --charcoal:#2a2a2a;
    --gray:#5e5a5a;
    --muted:#555555;
    --card-light:#3a3a3a;
    --card-dark:#161616;
    --silver-dark:#9a9a9a;
    --silver-light:#f2f2f2;
  }
  *{margin:0;padding:0;box-sizing:border-box}
  html,body{width:1200px;height:934px;overflow:hidden;background:var(--bg);font-family:"Open Sans",Arial,sans-serif;color:var(--ink)}
  .sheet{position:absolute;background:var(--paper);box-shadow:0 6px 10px rgba(0,0,0,.25);overflow:hidden}
  .sheet svg.art{position:absolute;inset:0;width:100%;height:100%}
  .brand{position:absolute;display:flex;align-items:center;gap:7px}
  .brand-mark{width:16px;height:16px;background:var(--charcoal);flex:none}
  .brand-text{display:flex;flex-direction:column;line-height:1}
  .brand-name{font-weight:700;font-size:21px;color:var(--charcoal);letter-spacing:.2px}
  .brand-tag{font-size:7.5px;letter-spacing:2.6px;color:var(--charcoal);margin-top:3px}
  .dot{display:inline-block;width:4px;height:4px;border-radius:50%;background:#777;flex:none}

  .letterhead{left:69px;top:83px;width:469px;height:665px}
  .letterhead .brand{left:40px;top:40px}
  .letterhead-contact{position:absolute;right:48px;top:560px;text-align:right;font-size:6.3px;line-height:11px;color:var(--muted)}
  .letterhead-contact .company{font-weight:700;color:var(--ink);font-size:6.8px;margin-bottom:3px}
  .letterhead-contact .row{display:flex;justify-content:flex-end;gap:6px;align-items:center}

  .envelope-front{left:565px;top:83px;width:566px;height:256px}
  .envelope-front .brand{left:30px;top:32px}
  .envelope-contact{position:absolute;left:28px;top:191px;font-size:6.3px;line-height:9px;color:var(--muted)}
  .envelope-contact .address{margin-bottom:7px}
  .envelope-contact .row{display:flex;gap:5px;align-items:center}

  .envelope-back{left:565px;top:366px;width:566px;height:255px}
  .envelope-url{position:absolute;left:0;right:0;top:40px;text-align:center;color:#e8e8e8;font-size:9px;letter-spacing:2px}

  .card{position:absolute;top:646px;width:121px;height:204px;box-shadow:0 6px 10px rgba(0,0,0,.3);overflow:hidden}
  .card .brand{left:0;right:0;flex-direction:column;gap:6px}
  .card .brand-text{align-items:center}
  .card .brand-name{font-size:16px}
  .card .brand-tag{font-size:5.5px;letter-spacing:1.3px;margin-top:2px}
  .card .brand-mark{width:14px;height:14px}

  .card-back{left:565px;background:linear-gradient(160deg,var(--card-light),var(--card-dark) 70%)}
  .card-back::after{content:"";position:absolute;left:0;right:0;bottom:0;height:9px;background:linear-gradient(90deg,var(--silver-dark),var(--silver-light),var(--silver-dark))}
  .card-back .brand{top:74px}
  .card-back .brand-name{color:#e4e4e4}
  .card-back .brand-tag{color:#d0d0d0}
  .card-back .brand-mark{background:#d8d8d8}

  .card-front{left:726px;background:var(--paper);color:var(--ink)}
  .card-front::before{content:"";position:absolute;left:0;top:0;bottom:0;width:6px;background:linear-gradient(180deg,var(--silver-dark),var(--silver-light),var(--silver-dark))}
  .card-front .brand{top:44px;left:6px}
  .person{position:absolute;left:17px;top:128px}
  .person-name{font-size:7.5px;font-weight:700;color:var(--ink)}
  .person-role{font-size:4.6px;color:var(--muted)}
  .card-contact{position:absolute;left:17px;top:162px;font-size:4.6px;line-height:7px;color:var(--muted)}
  .card-contact .row{display:flex;gap:4px;align-items:center}
  .card-contact .dot{width:3px;height:3px;background:#777}
</style>
</head>
<body>

<section class="sheet letterhead">
  <svg class="art" viewBox="0 0 469 665" preserveAspectRatio="none" aria-hidden="true">
    <path d="M0,0 L469,0 L469,30 C330,12 150,3 0,0 Z" fill="var(--ink)"/>
    <path d="M110,5 C290,14 420,30 469,42 L469,52 C400,36 250,18 110,5 Z" fill="var(--gray)"/>
    <path d="M0,598 C120,606 250,620 330,646 C230,638 100,630 0,620 Z" fill="var(--gray)"/>
    <path d="M0,628 C150,636 330,650 469,657 L469,665 L0,665 Z" fill="var(--ink)"/>
  </svg>
  <div class="brand">
    <span class="brand-mark"></span>
    <div class="brand-text"><span class="brand-name">Nordlink</span><span class="brand-tag">DIGITALE STRATEGIEN</span></div>
  </div>
  <div class="letterhead-contact">
    <div class="company">Nordlink LLC</div>
    <div>Your Commercial or office address</div>
    <div class="row" style="margin-top:4px">00.00.00.0000 <span class="dot"></span></div>
    <div class="row">yourname@yourwebsite.com <span class="dot"></span></div>
    <div class="row">www.yourwebsite.com <span class="dot"></span></div>
  </div>
</section>

<section class="sheet envelope-front">
  <svg class="art" viewBox="0 0 566 256" preserveAspectRatio="none" aria-hidden="true">
    <path d="M170,240 C340,214 480,196 566,182 L566,198 C450,212 300,228 170,240 Z" fill="var(--gray)"/>
    <path d="M0,250 C200,232 400,214 566,204 L566,256 L0,256 Z" fill="var(--ink)"/>
  </svg>
  <div class="brand">
    <span class="brand-mark"></span>
    <div class="brand-text"><span class="brand-name">Nordlink</span><span class="brand-tag">DIGITALE STRATEGIEN</span></div>
  </div>
  <div class="envelope-contact">
    <div class="address">Your Commercial or office address</div>
    <div class="row"><span class="dot"></span>00.00.00.0000</div>
    <div class="row"><span class="dot"></span>yourname@yourwebsite.com</div>
    <div class="row"><span class="dot"></span>www.yourwebsite.com</div>
  </div>
</section>

<section class="sheet envelope-back">
  <svg class="art" viewBox="0 0 566 255" preserveAspectRatio="none" aria-hidden="true">
    <path d="M0,0 L566,0 L523,91 L55,91 Z" fill="var(--ink)"/>
    <rect x="0" y="247" width="566" height="8" fill="var(--ink)"/>
  </svg>
  <div class="envelope-url">www.nordlink.com</div>
</section>

<section class="card card-back">
  <div class="brand">
    <span class="brand-mark"></span>
    <div class="brand-text"><span class="brand-name">Nordlink</span><span class="brand-tag">DIGITALE STRATEGIEN</span></div>
  </div>
</section>

<section class="card card-front">
  <div class="brand">
    <span class="brand-mark"></span>
    <div class="brand-text"><span class="brand-name">Nordlink</span><span class="brand-tag">DIGITALE STRATEGIEN</span></div>
  </div>
  <div class="person">
    <div class="person-name">Your Long Name</div>
    <div class="person-role">Managing Director</div>
  </div>
  <div class="card-contact">
    <div class="row"><span class="dot"></span>Your Commercial or office address</div>
    <div class="row"><span class="dot"></span>00.00.00.0000 &nbsp; 00.00.00.0000</div>
    <div class="row"><span class="dot"></span>yourname@yourwebsite.com</div>
    <div class="row"><span class="dot"></span>www.yourwebsite.com</div>
  </div>
</section>

</body>
</html>
```